New business card for a regional office of a US M&A company

We need business card for a finance company, office based in Hong Kong , our Head office is in US, our business is to Merge and acquires companies , the new office will be a regional office for the Asia Pacific region. We want to use the head office logo as attached ( but don't have to be exactly the same, can be a variation to it) as a base and then add Asia Pacific alongside the logo.
We would prefer to have be bilingual Eng + Chinese, although we don't really have Chinese company name .

Industry/Entity Type

Business

Contact Information for Business Card

Clara Jo Tsang
 

VP,
APAC M&A Operations
Orin Vantage Asia Pacific Limited
 
Unit 1407, K18
18 Tai Lok Shan Road, 
Hong Kong 
 
M: +852 6038 1742
T : +852 2836 4100
F : +852 2836 4177
VOIP: 4158
 
cjtsang@orinvantage.com

Font styles to use
Serif
Sans Serif

Colors

Designer to choose colors to be used in the design.

Requirements
Must have
• APAC Office

```html
<!DOCTYPE html>
<html lang="en">
<head>
<meta charset="utf-8">
<title>Orin Vantage Asia Pacific – Business Card</title>
<link href="https://fonts.googleapis.com/css2?family=Open+Sans:wght@400;700&family=Arimo:wght@700&display=swap" rel="stylesheet">
<style>
  :root {
    --navy: #10273f;
    --teal: #1eaad1;
    --white: #ffffff;
    --silver: #d3d6d9;
    --backdrop: #eceae7;
  }
  html, body {
    margin: 0;
    width: 1200px;
    height: 900px;
    overflow: hidden;
    background: var(--backdrop);
    font-family: "Open Sans", Arial, sans-serif;
  }
  .canvas { position: relative; width: 1200px; height: 900px; }

  .card { position: absolute; overflow: hidden; box-shadow: 0 6px 18px rgba(0,0,0,.18); }

  /* Front */
  .card-front { left: 77px; top: 34px; width: 589px; height: 363px; background: var(--white); }
  .card-front .bands { position: absolute; inset: 0; }
  .brand { position: absolute; left: 100px; top: 62px; display: flex; align-items: center; gap: 26px; }
  .brand-mark { width: 64px; height: 64px; background: var(--navy); }
  .brand-name {
    color: var(--teal); font-weight: 700; font-size: 33px; line-height: 36px; letter-spacing: .3px;
  }
  .voip { position: absolute; left: 6px; top: 201px; color: var(--white); font-size: 15px; letter-spacing: .3px; }

  .contact-list { position: absolute; left: 31px; top: 250px; margin: 0; padding: 0; list-style: none; color: var(--white); font-size: 15.5px; }
  .contact-list li { display: flex; align-items: center; height: 21.5px; }
  .contact-list svg { width: 12px; height: 12px; margin-right: 9px; fill: var(--white); }

  .person { position: absolute; right: 36px; top: 250px; text-align: right; color: var(--white); font-size: 15px; line-height: 21.5px; }
  .person-name { font-family: "Arimo", Arial, sans-serif; font-weight: 700; font-size: 19px; letter-spacing: .4px; line-height: 24px; }

  /* Back */
  .card-back { left: 388px; top: 505px; width: 567px; height: 352px; background: var(--navy); }
  .back-mark { position: absolute; left: 225px; top: 100px; width: 118px; height: 118px; background: var(--silver); }
  .back-name { position: absolute; left: 0; right: 0; top: 257px; text-align: center; color: var(--teal); font-weight: 700; font-size: 21px; letter-spacing: .6px; }
</style>
</head>
<body>
<main class="canvas">

  <section class="card card-front" aria-label="Business card front">
    <svg class="bands" viewBox="0 0 589 363" width="589" height="363" aria-hidden="true">
      <polygon points="0,199 403,199 375,225 0,225" fill="var(--teal)"/>
      <polygon points="383,226 415,192 589,192 589,363 0,363 0,226" fill="var(--navy)"/>
    </svg>

    <div class="brand">
      <div class="brand-mark"></div>
      <div class="brand-name">ORIN VANTAGE<br>ASIA PACIFIC LTD</div>
    </div>

    <div class="voip">VOIP: 4158</div>

    <ul class="contact-list">
      <li><svg viewBox="0 0 12 12"><path d="M2 1h2l1 3-1.5 1a6 6 0 0 0 3.5 3.5L8 7l3 1v2a1 1 0 0 1-1 1A9 9 0 0 1 1 2a1 1 0 0 1 1-1z"/></svg>+852 2836 4100</li>
      <li><svg viewBox="0 0 12 12"><path d="M3.5 0h5a1 1 0 0 1 1 1v10a1 1 0 0 1-1 1h-5a1 1 0 0 1-1-1V1a1 1 0 0 1 1-1zm.5 1.5v7.5h4V1.5z"/></svg>+852 6038 1742</li>
      <li><svg viewBox="0 0 12 12"><path d="M3 0h5v3H3zM1 4h10v8H1zm2 2v1h2V6zm3 0v1h2V6zM3 8v1h2V8zm3 0v1h2V8z"/></svg>+852 2836 4177</li>
      <li><svg viewBox="0 0 12 12"><path d="M0 2h12v8H0zm1 1v.5l5 3.2 5-3.2V3z"/></svg>cjtsang@orinvantage.com</li>
    </ul>

    <div class="person">
      <div class="person-name">CLARA JO TSANG VP</div>
      <div>APAC M&amp;A Operations</div>
      <div>Unit 1407, K18</div>
      <div>18 Tai Lok Shan Road, Hong Kong</div>
    </div>
  </section>

  <section class="card card-back" aria-label="Business card back">
    <div class="back-mark"></div>
    <div class="back-name">ORIN VANTAGE ASIA PACIFIC</div>
  </section>

</main>
</body>
</html>
```